Heritage Australian brand needs new packaging design to reflect the change to being 100% Recycled.

The heritage Australian brand - KLIV™ Fabric Combs have been sold to households worldwide (but mostly Australia) for over 40 years.

It was invented in Sydney in 1970, and since then many imitations are in the marketplace have copied it exactly. (colour, print colour) In fact, KLIV™ comb is a generic word for a fabric comb in the marketplace.

Our KLIV™ Fabric Comb will be a world first 100% recycled product that will be a different colour - Hex #606f61 or RGB 9611197, or as per Tarnova steel colour Wildnerness.

We need it to be differentiated from the "old" blue plastic to the new "green". sustainable product.

We need a design that is modern, yet retro/traditional, that takes us into a new era.

It sits with our other tool - the Super KLIV™ Fabric Comb that is already sustainably produced. (wooden handle, brass teeth, Australian steel)

Both combs are locally produced in Melbourne, Australia.

We need this for a calico bag that has 2 sizes.
Small: 110mm x 90mm (fits the small KLIV™)
Large: 250mm x 300mm - also has smaller inner pocket 100mm x 70mm to hold BOTH combs, seperately so they don't blunt the brass teeth.
The back of each of these bags has the Instructions on it, as well as logos - Southmark Pledge etc.

We also need Card Packaging designed for each of the Combs.

We have trademarked the KLIV™ logo and use the font Flash Bold.

We will want to add gift boxing later, so ideally the design can be easily transferred across different packaging options.

The final design should communicate heritage, honesty, stability, and integrity. (Think of Quelta toothpaste, Dorrin mustard, Pollwick Tandry is our aspirational competitor)

Also lean towards simple and bold design. In the original brief, I mention Quelta Toothpaste. Not in a design sense, but in the modern yet tradtional packaging. The KLIV™ Comb is such a simple tool, that I think a colourblock or simple bold design would align. KISS principle.

```html
<!DOCTYPE html>
<html lang="en">
<head>
<meta charset="utf-8">
<title>KLIV™ Fabric Comb Packaging</title>
<link rel="stylesheet" href="https://fonts.googleapis.com/css2?family=Oswald:wght@600;700&family=Archivo+Narrow:wght@400;600;700&display=swap">
<style>
  :root {
    --backdrop: #3a5a45;
    --calico: #ece5d4;
    --calico-seam: #ddd4bf;
    --ink: #2f5a3f;
    --ink-soft: #557060;
    --icon-tone: #cfd6c9;
  }
  * { margin: 0; padding: 0; box-sizing: border-box; }
  html, body { width: 1200px; height: 1200px; overflow: hidden; }
  body {
    background: var(--backdrop);
    position: relative;
    font-family: "Archivo Narrow", sans-serif;
    color: var(--ink);
  }
  .panel { position: absolute; background: var(--calico); }
  .seam { position: absolute; left: 0; right: 0; height: 1px; background: var(--calico-seam); }

  /* small front pouch */
  .pouch-front { left: 137px; top: 103px; width: 268px; height: 312px; }
  .hang-slot {
    position: absolute; left: 109px; top: 14px; width: 50px; height: 12px;
    border-radius: 6px; background: var(--backdrop);
  }
  .brand-word {
    font-family: "Oswald", sans-serif; font-weight: 700; color: var(--ink);
    text-align: center; position: absolute; left: 0; right: 0; line-height: 1;
  }
  .pouch-front .brand-word { top: 140px; font-size: 52px; }
  .product-lines { position: absolute; left: 0; right: 0; text-align: center; text-transform: uppercase; }
  .pouch-front .product-lines { top: 228px; font-size: 13px; font-weight: 700; line-height: 1.25; }
  .pouch-front .product-lines .minor { font-weight: 400; font-size: 11px; }

  /* back pouch */
  .pouch-back { left: 137px; top: 638px; width: 283px; height: 457px; padding: 28px 22px; }
  .back-title { font-size: 15px; font-weight: 600; text-transform: uppercase; letter-spacing: .5px; }
  .back-sub { font-size: 17px; font-weight: 600; text-transform: uppercase; margin-top: 2px; }
  .back-tag { font-size: 11px; line-height: 1.25; margin-top: 4px; }
  .back-label { font-size: 9px; font-weight: 600; text-transform: uppercase; margin-top: 18px; }
  .back-body { font-size: 6.5px; line-height: 1.35; margin-top: 6px; color: var(--ink-soft); }
  .steps { display: grid; grid-template-columns: repeat(3, 1fr); gap: 14px 8px; margin-top: 16px; }
  .step { display: flex; flex-direction: column; align-items: center; text-align: center; font-size: 6.5px; line-height: 1.3; color: var(--ink-soft); }
  .step-icon { width: 22px; height: 22px; border-radius: 50%; background: var(--icon-tone); margin-bottom: 4px; }
  .back-foot { position: absolute; left: 22px; right: 22px; bottom: 20px; display: flex; align-items: center; gap: 8px; }
  .cert-badge { width: 22px; height: 22px; border-radius: 50%; border: 1px solid var(--ink-soft); }
  .foot-note { font-size: 6.5px; line-height: 1.3; color: var(--ink-soft); margin-left: 10px; }

  /* large bag */
  .bag-large { left: 598px; top: 318px; width: 457px; height: 827px; }
  .bag-large .seam { top: 44px; }
  .bag-large .eyelet {
    position: absolute; left: 221px; top: 16px; width: 14px; height: 14px;
    border-radius: 50%; background: var(--backdrop);
  }
  .bag-large .brand-word { top: 318px; font-size: 118px; }
  .bag-large .product-lines { top: 558px; font-size: 24px; font-weight: 700; line-height: 1.2; }
  .bag-large .product-lines .minor { font-size: 17px; font-weight: 600; }
</style>
</head>
<body>

  <section class="panel pouch-front" aria-label="Small bag front">
    <div class="hang-slot"></div>
    <div class="seam" style="top:40px"></div>
    <div class="brand-word">KLIV™</div>
    <div class="product-lines">
      <div>Super KLIV™ Fabric Comb</div>
      <div>100% Recycled</div>
      <div class="minor">(Est. 1970)</div>
    </div>
  </section>

  <section class="panel pouch-back" aria-label="Bag back with instructions">
    <div class="seam" style="top:14px"></div>
    <div class="back-title">Instructions</div>
    <div class="back-sub">Classic KLIV™</div>
    <div class="back-tag">The trusted fabric comb with<br>Australian heritage, for everyone</div>
    <div class="back-label">Full Back</div>
    <p class="back-body">Lay the garment flat and hold the fabric taut. Draw the comb gently across pilled areas in short strokes. Lift away fluff as you go and repeat until smooth. Store the comb in its pocket to keep the brass teeth sharp.</p>
    <div class="steps">
      <div class="step"><span class="step-icon" role="img" aria-label="Icon of a garment laid flat"></span>Lay garment flat on a table</div>
      <div class="step"><span class="step-icon" role="img" aria-label="Icon of comb stroke direction"></span>Comb gently in one direction</div>
      <div class="step"><span class="step-icon" role="img" aria-label="Icon of fluff being lifted"></span>Lift fluff away as you go</div>
      <div class="step"><span class="step-icon" role="img" aria-label="Icon of a knitted jumper"></span>Works on wool and knits</div>
      <div class="step"><span class="step-icon" role="img" aria-label="Icon of a fabric care check"></span>Check fabric before you begin</div>
      <div class="step"><span class="step-icon" role="img" aria-label="Icon of storage pocket"></span>Store safely in the pocket</div>
    </div>
    <div class="back-foot">
      <span class="cert-badge"></span>
      <span class="cert-badge"></span>
      <span class="foot-note">Made in Melbourne Australia<br>100% recycled</span>
    </div>
  </section>

  <section class="panel bag-large" aria-label="Large calico bag front">
    <div class="eyelet"></div>
    <div class="seam"></div>
    <div class="brand-word">KLIV™</div>
    <div class="product-lines">
      <div>Super KLIV™ Fabric Comb</div>
      <div>Est. Melb 1970</div>
      <div class="minor">(100% Recycled)</div>
    </div>
  </section>

</body>
</html>
```